Corwin Beacon Lighting - Commercial & Residential Landscape Lighting

Landscape Lighting Services & Design: Create a website for our landscape lighting company. We would like the design to be tailored around this description:
Illuminate with Confidence. Designed with Precision. Installed with Care.
Locally and veteran-owned, we take pride in transforming outdoor spaces through innovative lighting solutions tailored to your vision. From landscape and holiday lighting to permanent installations, our effortless process and expert design deliver breathtaking results and lasting curb appeal. Backed by a lifetime warranty and quarterly service options, our commitment to quality and customer satisfaction is unwavering. Try before you buy and experience your home in a whole new light with our complimentary demo kit — see the stunning effects before you decide.
- Also, add in this information as well; Outdoor Lighting not only beautifies spaces but also significantly enhances safety by illuminating your home or business. Beautifully lit entrances deter potential intruders, making your home a safer place for your loved ones. we also offer quarterly service plans to ensure lighting equipment continues to operate & illuminate effectively throughout the year. Also mention we provide free estimates and we are offering a 10% discount to military, veterans, and first responders.

Target Market(s)

Luxury market

Industry/Entity Type

Landscape Lighting - Residential & Commercial Lighting Services

Coding

Coded - Design and coding required

Number of Pages Required

2 page

Colors
00AB8E
00BBA5
67D7C9
C6EFE9
E9F9F6
59FF00
82FF00
B8FF75
E3FFCB
F4FFEA
FFC000
F8CF3A
FAE287
FDF2CF
FEFAEE

Requirements
Must have
• a lead generation button where people can submit their information for us to reach out to them and schedule their free estimate, homepage, about page, contact page, products and services page, user friendly, easy to navigate, and it also must be engaging and eye popping, as well as appealing to the luxury market. Please use colors; verdent green, dark green, ivory, and sunny yellow. Also, include an about page that references our story; Derek is retired Army and he opened a fitness studio in 2017 with his wife Jolene. He has installed low voltage lighting in every home he lived in and for his friends and family over the years and decided to open his own business because he is passionate about beautifying outdoor landscapes and highlighting a properties full potential, not only in the day but at night as well all while providing safety and security for his clients. Having a deep respect for nature and landscaping, he wants to provide the same care and quality to each of his clients as he has in the fitness industry for decades. He believes small businesses are the back bone of America and he's excited to provide a service that is all to often neglected in the design of a home.
Nice to have
• I would like to have a clear intent and purpose, engaging web design, clear call to action, optimized for search engines, mobile friendy design, security measures, credibility indicators

```html
<!DOCTYPE html>
<html lang="en">
<head>
<meta charset="UTF-8">
<title>Corwin Beacon Lighting – Commercial &amp; Residential Landscape Lighting</title>
<link href="https://fonts.googleapis.com/css2?family=Poppins:wght@400;500;600;700&family=Roboto:wght@300;400;500;700&display=swap" rel="stylesheet">
<style>
:root{
  --forest:#1b3a1a;
  --forest-deep:#163016;
  --verdant:#2a6630;
  --heading-green:#2f6a33;
  --ivory:#f6f1e6;
  --white:#ffffff;
  --sun:#fad93a;
  --sun-soft:#fbe06a;
  --ink:#1f1f1f;
  --field:#f4f4f4;
  --field-line:#e2e2e2;
}
*{box-sizing:border-box;margin:0;padding:0}
html,body{width:1200px;height:5076px;overflow:hidden}
body{font-family:"Poppins",sans-serif;color:var(--ink);background:var(--white);position:relative}
section,header,footer{position:absolute;left:0;width:1200px}
.abs{position:absolute}
.photo{position:absolute}

/* Hero */
.hero{top:0;height:514px;background:var(--forest);overflow:visible}
.hero-photo{left:380px;top:0;width:820px;height:514px;
  background:radial-gradient(ellipse at 62% 55%,#8a5a2c 0%,#5a3a1f 28%,#2d3a22 58%,transparent 80%),
  linear-gradient(90deg,var(--forest) 0%,#2a3f24 30%,#3d3a26 60%,#26331f 100%)}
.logo{left:112px;top:34px;color:var(--sun);font-family:"Poppins",sans-serif;font-weight:500;line-height:1}
.logo .name{font-size:38px;letter-spacing:1px;display:block}
.logo .sub{font-size:10px;letter-spacing:2.4px;display:block;margin-top:4px}
.nav{left:441px;top:44px;display:flex;gap:0;font-size:14px;color:#e9ecdf}
.nav a{color:inherit;text-decoration:none;position:absolute;white-space:nowrap}
.nav .active{font-weight:600;color:#fff}
.btn{display:inline-flex;align-items:center;justify-content:center;font-family:"Poppins",sans-serif;font-weight:700;text-transform:uppercase;border-radius:4px 14px 4px 14px;text-decoration:none}
.btn-sun{background:var(--sun);color:var(--forest)}
.btn-green{background:var(--verdant);color:#fff}
.nav-cta{left:912px;top:33px;width:176px;height:46px;font-size:13px}
.hero-title{left:112px;top:170px;font-family:"Roboto",sans-serif;font-weight:300;font-size:37px;line-height:52px;color:#fff}
.hero-title b{font-weight:700}
.hero-cta{left:112px;top:356px;width:178px;height:43px;font-size:13px}
.discount{left:940px;top:363px;width:224px;height:224px;border-radius:50%;background:var(--sun-soft);z-index:3}
.discount-inner{position:absolute;left:12px;top:12px;width:200px;height:200px;border-radius:50%;background:var(--sun);text-align:center;color:var(--forest)}
.discount .pct{margin-top:32px;font-size:38px;font-weight:700;line-height:1}
.discount .pct small{font-size:20px}
.discount .lbl{font-size:18px;font-weight:700;margin-top:6px}
.discount .who{font-size:14px;line-height:17px;margin-top:8px;color:#3a3a1a}

/* shared headings */
.eyebrow{font-family:"Roboto",sans-serif;font-weight:400;font-size:27px;color:var(--heading-green);line-height:1}
.title{font-family:"Roboto",sans-serif;font-weight:500;font-size:39px;color:var(--forest);line-height:1.1;text-transform:uppercase}
.center{left:0;width:1200px;text-align:center}
.frame{position:absolute;border:12px solid var(--verdant)}

/* About */
.about{top:514px;height:1035px;background:var(--ivory)}
.about-photo{left:114px;top:97px;width:382px;height:427px;background:linear-gradient(160deg,#3d4a3a 0%,#2a2f25 45%,#5a4a2a 80%,#8a6a30 100%)}
.about-eyebrow{left:558px;top:126px}
.about-title{left:558px;top:158px}
.about-text{left:558px;top:232px;width:548px;font-size:14.5px;line-height:25.7px;color:#2a2a2a}
.safety{left:114px;top:581px;width:380px;font-size:14.5px;line-height:25.7px;color:#2a2a2a}
.safety strong{font-weight:600;color:var(--ink)}
.safety-cta{left:114px;top:818px;width:280px;height:44px;font-size:13px}
.safety-frame{left:630px;top:599px;width:490px;height:320px;border-top:none;border-left:none}
.safety-photo{left:524px;top:566px;width:566px;height:317px;background:linear-gradient(180deg,#5e6a8a 0%,#b88a7a 28%,#6a5a4a 55%,#2e3328 80%,#3a3f2e 100%)}

/* Services */
.services{top:1549px;height:737px;background:var(--white)}
.svc-eyebrow{top:136px}
.svc-title{top:175px}
.card{top:244px;width:479px;height:426px;background:var(--forest)}
.card .photo{left:0;top:0;width:479px;height:207px}
.card h3{position:absolute;left:27px;top:252px;font-family:"Roboto",sans-serif;font-weight:500;font-size:23px;color:#fff}
.card p{position:absolute;left:27px;top:316px;width:420px;font-size:13.5px;line-height:25px;color:#dfe6da}
.card-a{left:112px}
.card-a .photo{background:linear-gradient(180deg,#3b4757 0%,#2f3540 40%,#8a5a2a 70%,#3a2a1a 100%)}
.card-b{left:609px}
.card-b .photo{background:linear-gradient(180deg,#6f8aa6 0%,#c9cfd6 35%,#4a4f40 65%,#1f2a1c 100%)}

/* Story */
.story{top:2286px;height:847px;background:var(--white)}
.story-eyebrow{top:96px}
.story-title{top:134px;text-transform:none}
.story-text{left:110px;top:228px;width:492px;font-size:14.5px;line-height:25.7px;color:#2a2a2a}
.story-text strong{font-weight:600;color:var(--ink)}
.story-text p+p{margin-top:14px}
.story-frame{left:731px;top:271px;width:388px;height:449px;border-top:none;border-left:none}
.story-photo{left:642px;top:222px;width:446px;height:467px;background:linear-gradient(180deg,#1e2a1c 0%,#2f4a2a 40%,#4a6a2e 65%,#2a3a1e 100%)}

/* Projects */
.projects{top:3133px;height:876px;background:var(--ivory)}
.proj-eyebrow{top:121px}
.proj-title{top:160px}
.proj-frame{left:213px;top:468px;width:295px;height:296px;border-top:none}
.proj-1{left:114px;top:257px;width:306px;height:471px;background:linear-gradient(180deg,#2a3850 0%,#1e2a24 40%,#6a3a22 62%,#2a3220 100%)}
.proj-2{left:441px;top:257px;width:318px;height:223px;background:linear-gradient(180deg,#2c3a4a 0%,#1e2a1e 45%,#6a4a2a 65%,#3a4a28 100%)}
.proj-3{left:441px;top:504px;width:318px;height:224px;background:linear-gradient(180deg,#24303c 0%,#6a6a5a 40%,#4a3a22 70%,#1e221a 100%)}
.proj-4{left:782px;top:257px;width:306px;height:471px;background:linear-gradient(180deg,#3a4a5a 0%,#2a3220 35%,#7a5a2a 55%,#8a7a2a 100%)}

/* Contact */
.contact{top:4009px;height:759px;background:var(--white)}
.contact-frame{left:124px;top:150px;width:952px;height:516px;border-top:none}
.contact-frame-top-l{left:124px;top:150px;width:300px;height:12px;background:var(--verdant)}
.contact-frame-top-r{left:776px;top:150px;width:300px;height:12px;background:var(--verdant)}
.contact-eyebrow{top:147px}
.contact-title{top:184px}
.field{position:absolute;background:var(--field);border:1px solid var(--field-line);border-radius:6px;font-size:13px;color:#8a8a8a;padding:0 26px;display:flex;align-items:center}
.f-name{left:272px;top:260px;width:654px;height:55px}
.f-phone{left:272px;top:335px;width:317px;height:55px}
.f-email{left:611px;top:335px;width:315px;height:55px}
.f-msg{left:272px;top:406px;width:654px;height:112px;align-items:flex-start;padding-top:22px}
.contact-cta{left:459px;top:548px;width:280px;height:41px;font-size:13px}

/* Footer */
.footer{top:4768px;height:308px;background:var(--forest-deep);color:#fff}
.foot-logo{left:110px;top:64px;color:#fff;font-family:"Poppins",sans-serif;font-weight:500;line-height:1}
.foot-logo .name{font-size:48px;letter-spacing:1px;display:block}
.foot-logo .sub{font-size:12px;letter-spacing:3px;display:block;margin-top:6px}
.foot-col{top:58px;font-size:13.5px;line-height:27px}
.foot-col h4{font-size:14px;font-weight:600;margin-bottom:8px;text-transform:uppercase}
.foot-col a{color:#fff;text-decoration:none;display:block}
.col-quick{left:384px}
.col-other{left:638px}
.col-contact{left:869px}
.contact-line{display:flex;gap:14px;align-items:flex-start}
.contact-line svg{flex:none;margin-top:7px}
.copyright{top:262px;left:0;width:1200px;text-align:center;font-size:13.5px;color:#e6e6e6}
</style>
</head>
<body>

<header class="hero">
  <div class="photo hero-photo" role="img" aria-label="Brick home with arched window lit by warm landscape lights at dusk"></div>
  <div class="abs logo"><span class="name">CORWIN</span><span class="sub">BEACON LIGHTING</span></div>
  <nav class="abs nav">
    <a class="active" style="left:0">Home</a>
    <a style="left:87px">About</a>
    <a style="left:170px">Products and Services</a>
    <a style="left:377px">Contact</a>
  </nav>
  <a class="abs btn btn-sun nav-cta">Book Free Demo</a>
  <h1 class="abs hero-title">Illuminate with <b>Confidence.</b><br>Designed with <b>Precision.</b><br>Installed with <b>Care.</b></h1>
  <a class="abs btn btn-green hero-cta">Book Free Demo</a>
  <div class="abs discount">
    <div class="discount-inner">
      <div class="pct">10<small>%</small></div>
      <div class="lbl">DISCOUNT</div>
      <div class="who">Military, veterans,<br>and first<br>responders.</div>
    </div>
  </div>
</header>

<section class="about">
  <div class="photo about-photo" role="img" aria-label="Installer placing a landscape light among garden stones at dusk"></div>
  <div class="abs eyebrow about-eyebrow">ABOUT US</div>
  <h2 class="abs title about-title">Corwin Beacon Lighting</h2>
  <p class="abs about-text">Locally and veteran-owned, we take pride in transforming outdoor spaces through innovative lighting solutions tailored to your vision. From landscape and holiday lighting to permanent installations, our effortless process and expert design deliver breathtaking results and lasting curb appeal. Backed by a lifetime warranty and quarterly service options, our commitment to quality and customer satisfaction is unwavering. Try before you buy and experience your home in a whole new light with our complimentary demo kit — see the stunning effects before you decide.</p>
  <p class="abs safety"><strong>Outdoor Lighting not only beautifies spaces but also significantly enhances safety by illuminating your home or business.</strong><br>Beautifully lit entrances deter potential intruders, making your home a safer place for your loved ones. we also offer quarterly service plans to ensure lighting equipment continues to operate &amp; illuminate effectively throughout the year.</p>
  <a class="abs btn btn-sun safety-cta">Schedule Free Estimates</a>
  <div class="frame safety-frame"></div>
  <div class="photo safety-photo" role="img" aria-label="Modern two-storey home glowing with exterior lighting at sunset"></div>
</section>

<section class="services">
  <div class="abs eyebrow center svc-eyebrow">WHAT WE DO</div>
  <h2 class="abs title center svc-title">Corwin Services</h2>
  <article class="abs card card-a">
    <div class="photo" role="img" aria-label="Commercial building with lit landscaping at night"></div>
    <h3>Commercial Landscape Lighting</h3>
    <p>Sed ut perspiciatis unde omnis iste natus luptatecusan tium doloremque laudantium, totam rem</p>
  </article>
  <article class="abs card card-b">
    <div class="photo" role="img" aria-label="Modern residence with illuminated steps and garden"></div>
    <h3>Residential Landscape Lighting</h3>
    <p>Sed ut perspiciatis unde omnis iste natus luptatecusan tium doloremque laudantium, totam rem</p>
  </article>
</section>

<section class="story">
  <div class="abs eyebrow center story-eyebrow">OUR STORY</div>
  <h2 class="abs title center story-title">Corwin Beacon Lighting</h2>
  <div class="abs story-text">
    <p><strong>Derek, a retired Army veteran, has always had a passion for transforming spaces.</strong><br>In 2017, he and his wife Jolene opened a fitness studio, driven by a shared commitment to health, community, and quality service. Over the years, Derek’s interest in outdoor lighting grew as he installed low voltage lighting in his own homes and for friends and family, discovering how the right lighting can completely redefine a property’s beauty, safety, and functionality. That passion led him to launch his own lighting business, with a mission to help homeowners enhance their outdoor spaces and showcase their property’s full potential — not just during the day, but long after the sun goes down.</p>
    <p>With deep respect for nature, landscaping, and craftsmanship, Derek brings the same care and dedication to his lighting projects as he has in the fitness industry for decades. He believes small businesses are the heart of America and is proud to offer a service that adds value, character, and safety to homes in the community.</p>
  </div>
  <div class="frame story-frame"></div>
  <div class="photo story-photo" role="img" aria-label="Bollard light glowing beside a garden bed and lawn at night"></div>
</section>

<section class="projects">
  <div class="abs eyebrow center proj-eyebrow">OUR WORK</div>
  <h2 class="abs title center proj-title">Featured Projects</h2>
  <div class="frame proj-frame"></div>
  <div class="photo proj-1" role="img" aria-label="Brick house facade uplit at night beneath tall pines"></div>
  <div class="photo proj-2" role="img" aria-label="Lit home across a wide lawn at dusk"></div>
  <div class="photo proj-3" role="img" aria-label="House gable and walkway lit at night"></div>
  <div class="photo proj-4" role="img" aria-label="Home with warm accent lighting across a green lawn"></div>
</section>

<section class="contact">
  <div class="frame contact-frame"></div>
  <div class="abs contact-frame-top-l"></div>
  <div class="abs contact-frame-top-r"></div>
  <div class="abs eyebrow center contact-eyebrow">CONTACT US</div>
  <h2 class="abs title center contact-title">Get in Touch</h2>
  <div class="field f-name">Full Name</div>
  <div class="field f-phone">Phone Number</div>
  <div class="field f-email">Email ID</div>
  <div class="field f-msg">Message</div>
  <a class="abs btn btn-sun contact-cta">Schedule Free Estimates</a>
</section>

<footer class="footer">
  <div class="abs foot-logo"><span class="name">CORWIN</span><span class="sub">BEACON LIGHTING</span></div>
  <div class="abs foot-col col-quick">
    <h4>Quick Links</h4>
    <a>Home</a><a>Products and Services</a><a>About Us</a>
  </div>
  <div class="abs foot-col col-other">
    <h4>Other Links</h4>
    <a>Contact Us</a><a>Terms of Service</a><a>Privacy Policy</a>
  </div>
  <div class="abs foot-col col-contact">
    <h4>Contact Us</h4>
    <div class="contact-line">
      <svg width="12" height="14" viewBox="0 0 12 14" aria-hidden="true"><path d="M6 0a5 5 0 0 0-5 5c0 3.6 5 9 5 9s5-5.4 5-9a5 5 0 0 0-5-5zm0 7a2 2 0 1 1 0-4 2 2 0 0 1 0 4z" fill="#fff"/></svg>
      <span>Corwin,<br>Address Comes Here</span>
    </div>
    <div class="contact-line">
      <svg width="13" height="13" viewBox="0 0 13 13" aria-hidden="true"><path d="M3 0.5l2 2.6-1.2 1.6a7.5 7.5 0 0 0 4.5 4.5l1.6-1.2 2.6 2-1.2 2.4C5.6 12.4.6 7.4.6 1.7z" fill="#fff"/></svg>
      <span>+1 555-014-2270</span>
    </div>
    <div class="contact-line">
      <svg width="13" height="10" viewBox="0 0 13 10" aria-hidden="true"><rect x="0" y="0" width="13" height="10" rx="1" fill="#fff"/><path d="M0.5 1l6 4.5 6-4.5" stroke="#163016" stroke-width="1.2" fill="none"/></svg>
      <span>info@corwinbeacon.com</span>
    </div>
  </div>
  <div class="abs copyright">© 2025 Corwin. All Rights Reserved.</div>
</footer>

</body>
</html>
```